professional business card design for technology company

We are a small technology consulting firm, specialising in consulting based around Cloud and Managed services. Our colour scheme is yellow, blue and white, as you can see in the logos. Although we are based in melbourne australia, due to the nature of our work, our clients can be located anywhere. We are looking for a clean, professional, positive look - similar to our company logo

Target Market(s)

small business

Industry/Entity Type

Business

Contact Information for Business Card

eye catching, designed to incorporate some level of raised printing. Must contain website address, phone number, name and job title

Requirements
Must have
• Logo (attached) - use of the same colour scheme

```html
<!DOCTYPE html>
<html lang="en">
<head>
<meta charset="utf-8">
<title>Solvara Business Card</title>
<link rel="stylesheet" href="https://fonts.googleapis.com/css2?family=Lato:wght@400;700;900&display=swap">
<style>
  :root {
    --stage: #15191c;
    --sky: #50d1fb;
    --sun: #f6e20c;
    --paper: #ffffff;
    --slate: #3f4a48;
    --slate-card: #48534f;
    --ink-light: #ffffff;
  }
  * { margin: 0; padding: 0; box-sizing: border-box; }
  html, body { width: 1200px; height: 864px; overflow: hidden; }
  body {
    background: var(--stage);
    font-family: "Lato", Arial, sans-serif;
    position: relative;
  }
  .card {
    position: absolute;
    left: 362px;
    width: 503px;
    height: 295px;
    box-shadow: 0 3px 8px rgba(0,0,0,0.55);
    overflow: hidden;
  }
  .card--front { top: 103px; background: var(--paper); }
  .card--back {
    top: 458px;
    background: radial-gradient(circle at 35% 45%, #4e5a57 0%, var(--slate-card) 60%, #434d4a 100%);
  }
  .contact-panel {
    position: absolute;
    left: 0; top: 0;
    width: 241px; height: 100%;
    background: var(--sky);
    color: var(--ink-light);
  }
  .person-name {
    position: absolute;
    left: 26px; top: 26px;
    font-size: 22px; font-weight: 400;
    letter-spacing: 0.2px;
  }
  .person-title {
    position: absolute;
    left: 26px; top: 52px;
    font-size: 15px; color: var(--sun);
  }
  .contact-list {
    position: absolute;
    left: 26px; top: 150px;
    list-style: none;
  }
  .contact-item {
    display: flex; align-items: flex-start;
    font-size: 15px; line-height: 21.5px;
  }
  .contact-item--address { font-size: 13px; line-height: 16px; margin-top: 3px; }
  .contact-icon {
    width: 10px; height: 10px; flex: none;
    margin: 6px 5px 0 0; fill: var(--sun);
  }
  .contact-item--address .contact-icon { margin-top: 3px; }
  .wordmark {
    position: absolute;
    display: flex; align-items: center; gap: 10px;
    font-weight: 900; letter-spacing: -0.5px;
  }
  .wordmark-dot { border-radius: 50%; background: var(--sun); flex: none; }
  .wordmark--front { left: 264px; top: 122px; font-size: 34px; color: var(--slate); }
  .wordmark--front .wordmark-dot { width: 30px; height: 30px; }
  .wordmark--back { left: 136px; top: 134px; font-size: 38px; color: var(--ink-light); }
  .wordmark--back .wordmark-dot { width: 34px; height: 34px; }
</style>
</head>
<body>
  <section class="card card--front" aria-label="Business card front">
    <div class="contact-panel">
      <h1 class="person-name">Mara Linden</h1>
      <p class="person-title">Managing Director</p>
      <ul class="contact-list">
        <li class="contact-item">
          <svg class="contact-icon" viewBox="0 0 10 10" aria-hidden="true"><path d="M1 3.5C1 2 2.5 1.5 5 1.5S9 2 9 3.5V4.5H7V3.5H3V4.5H1Z"/><rect x="2" y="5" width="6" height="4" rx="1"/></svg>
          044-987 650 321
        </li>
        <li class="contact-item">
          <svg class="contact-icon" viewBox="0 0 10 10" aria-hidden="true"><path d="M3 0.5h4a1 1 0 0 1 1 1v7a1 1 0 0 1-1 1H3a1 1 0 0 1-1-1v-7a1 1 0 0 1 1-1Zm0.5 1.5v5.5h3V2Z"/></svg>
          044-987 650 321
        </li>
        <li class="contact-item">
          <svg class="contact-icon" viewBox="0 0 10 10" aria-hidden="true"><path d="M0.5 2h9v6h-9Z M1 2.5 5 5.5 9 2.5" stroke="#50d1fb" stroke-width="0.8"/></svg>
          hello@solvara.com
        </li>
        <li class="contact-item">
          <svg class="contact-icon" viewBox="0 0 10 10" aria-hidden="true"><g fill="none" stroke="#f6e20c" stroke-width="1.4"><rect x="0.8" y="4.2" width="5" height="3" rx="1.5" transform="rotate(-45 3.3 5.7)"/><rect x="4.2" y="2.8" width="5" height="3" rx="1.5" transform="rotate(-45 6.7 4.3)"/></g></svg>
          www.solvara.com
        </li>
        <li class="contact-item contact-item--address">
          <svg class="contact-icon" viewBox="0 0 10 10" aria-hidden="true"><path d="M5 0.3a3.3 3.3 0 0 1 3.3 3.3C8.3 6 5 9.7 5 9.7S1.7 6 1.7 3.6A3.3 3.3 0 0 1 5 0.3Zm0 2a1.3 1.3 0 1 0 0 2.6 1.3 1.3 0 0 0 0-2.6Z"/></svg>
          <span>48 Harbour Lane, Suite 2<br>Melbourne VIC, 3000</span>
        </li>
      </ul>
    </div>
    <div class="wordmark wordmark--front">
      <span class="wordmark-dot" aria-hidden="true"></span>
      <span class="wordmark-name">Solvara</span>
    </div>
  </section>

  <section class="card card--back" aria-label="Business card back">
    <div class="wordmark wordmark--back">
      <span class="wordmark-dot" aria-hidden="true"></span>
      <span class="wordmark-name">Solvara</span>
    </div>
  </section>
</body>
</html>
```